AMBER AND SLATE WEB

We need a home design in wordpress, we have now a web but we would like to improve it. Our current web is www.amberandslatevillas.example Our business is holliday rental of villas in Ibiza. Our guest must know that we are a reliable company, professional and with experience and good reviews. We want them to click in our reservation engine: https://bookings.amberandslatevillas.example/en/ and make reservation in our website. We would also like to say that all the properties that we have are just us who commercialize so we have best price available. Many people are going to see our villas in staylist.example and look to our website to make a reservation with us so we need to show them that they are at the right place and click at our link to our reservation engine. What make us special is that we are a local company, we are from Ibiza, Our guests are always received in person by the Amber and Slate Ibiza team. You will enjoy extensive tourist information when you check in and during the entire stay. You will be attended by ChatterLine and calls, always happy to help so that you have a happy and fun stay! Our guest stay is better than in hotel as they have more spece, private swiming pool, private garden, barbeque ... To rent a villa is the best way to stay in Ibiza. We also have a promotional video: https://vidshare.example/Qm7TzR2pLxA Let our philosophy be shown, we think that coming on holiday to Ibiza implies seeing the nature that we have in Ibiza, hence our name AMBER AND SLATE, like the pins that almost touch the sea in Ibiza, or the posidonea meadows where the intense green of the seaweed and the blue of the sea. We are aware of the environment, and we love Ibiza. For us, the client who visits Ibiza, should rent a car, go around the island, eat in a restaurant one day in front of the sea, is a night of partying to the discs, go shopping, visit the ancient heritage of Umanity, make some aquatic sport, enjoy the pool, those are for us Ibiza.

Target Market(s)

Europe, people from Holand, UK, Germany, France, Spain ...

Industry/Entity Type

Tourism

Colors

Designer to choose colors to be used in the design.

Requirements
Must have
• Pictures of Ibiza.
Nice to have
• Our name Amber and Slate Ibiza is beacuse in Ibiza there is forest that almost touch the watter of the Mediterranean sea, so you can see green of the forest and blue of the sea and the sky. And also beacause under the watter of the sea there is a plant called Posidonia that is also green please see the picture of posidonia.

```html
<!DOCTYPE html>
<html lang="en">
<head>
<meta charset="utf-8">
<title>Amber and Slate Ibiza — Villas &amp; The Countryside</title>
<link href="https://fonts.googleapis.com/css2?family=Montserrat:wght@400;500;600;700&family=Open+Sans:wght@400;600&family=Playfair+Display:ital,wght@1,400;1,700&display=swap" rel="stylesheet">
<style>
:root{
  --blue:#2f7de1;
  --blue-dark:#1f5fb8;
  --ink:#222;
  --text:#555;
  --muted:#999;
  --line:#e6e6e6;
  --faint:#f0f0f0;
  --footer:#141414;
  --footer-text:#9a9a9a;
  --white:#fff;
}
*{box-sizing:border-box;margin:0;padding:0}
html,body{width:1200px;height:3584px;overflow:hidden;background:var(--white)}
body{font-family:"Open Sans",Arial,sans-serif;color:var(--text);font-size:12px}
.page{position:relative;width:1200px;height:3584px;overflow:hidden}
.abs{position:absolute;left:0;width:1200px}

/* top bar */
.topbar{top:0;height:32px;border-top:3px solid var(--blue);border-bottom:1px solid var(--line);display:flex;align-items:center;justify-content:space-between;padding:0 40px;font-size:10px;color:var(--muted)}
.topbar .group{display:flex;gap:22px;align-items:center}
.topbar span{display:flex;align-items:center;gap:6px}
.topbar svg{width:10px;height:10px;fill:var(--blue)}

/* header */
.header{top:32px;height:80px;display:flex;align-items:center;justify-content:space-between;padding:0 40px}
.brand{display:flex;align-items:center;gap:10px;font-family:"Montserrat",sans-serif;font-weight:600;font-size:14px;color:#2a6e3a;letter-spacing:.5px}
.brand .mark{width:22px;height:22px;border-radius:50%;background:#2a6e3a}
.nav{display:flex;gap:30px;align-items:center;font-family:"Montserrat",sans-serif;font-size:10px;font-weight:600;color:var(--ink);letter-spacing:.5px}
.btn-outline{border:1.5px solid var(--ink);padding:9px 18px;font-size:10px;font-weight:600;font-family:"Montserrat",sans-serif;letter-spacing:.5px;color:var(--ink)}

/* hero */
.hero{top:112px;height:448px;background:
 radial-gradient(ellipse 300px 260px at 30px 380px,#2f5a2a 0%,rgba(47,90,42,0) 100%),
 radial-gradient(ellipse 320px 240px at 1130px 360px,#6b7a4a 0%,rgba(107,122,74,0) 100%),
 linear-gradient(180deg,#8fc3ea 0%,#b9dcf2 26%,#3f8fb8 34%,#1d6f9c 55%,#2aa5b5 80%,#8cd1c8 100%);
 display:flex;flex-direction:column;align-items:center;padding-top:76px;text-align:center;color:var(--white)}
.hero-script{font-family:"Playfair Display",serif;font-style:italic;font-size:44px;font-weight:400;text-shadow:0 2px 8px rgba(0,0,0,.25)}
.hero-title{font-family:"Playfair Display",serif;font-style:italic;font-weight:700;font-size:30px;margin-top:16px;text-transform:uppercase;text-shadow:0 2px 8px rgba(0,0,0,.3)}
.btn-ghost{margin-top:24px;border:1.5px solid var(--white);padding:9px 20px;font-family:"Montserrat",sans-serif;font-size:9px;font-weight:600;letter-spacing:1px}

/* search */
.search{position:absolute;top:472px;left:240px;width:720px;height:168px;background:var(--white);box-shadow:0 6px 24px rgba(0,0,0,.12);padding:24px 28px;display:grid;grid-template-columns:repeat(3,1fr);grid-template-rows:1fr 1fr;gap:14px 20px}
.field label{display:block;font-size:9px;color:var(--ink);font-weight:600;margin-bottom:5px}
.field .input{height:30px;border:1px solid var(--line);display:flex;align-items:center;padding:0 10px;gap:8px;font-size:9px;color:var(--muted)}
.field .input svg{width:10px;height:10px;fill:none;stroke:var(--blue);stroke-width:2}
.btn-search{align-self:end;height:30px;background:var(--blue);color:var(--white);display:flex;align-items:center;justify-content:center;gap:6px;font-family:"Montserrat",sans-serif;font-size:9px;font-weight:600;letter-spacing:.5px}

/* section heads */
.section-head{text-align:center;position:relative;height:60px}
.section-head .ghost{font-family:"Montserrat",sans-serif;font-weight:700;font-size:40px;color:var(--faint);letter-spacing:3px;text-transform:uppercase;line-height:40px}
.section-head h2{position:absolute;left:0;right:0;top:24px;font-family:"Playfair Display",serif;font-weight:700;font-size:15px;color:var(--ink);letter-spacing:1px;text-transform:uppercase}

.explore-head{top:704px}
.carousel{top:784px;height:256px;display:flex;gap:12px;padding:0 64px}
.slide{flex:1;position:relative;height:256px}
.slide .cap{position:absolute;left:0;right:0;bottom:0;height:26px;background:rgba(0,0,0,.45);color:var(--white);font-size:9px;font-family:"Montserrat",sans-serif;display:flex;align-items:center;justify-content:center;letter-spacing:.5px}
.arrow{position:absolute;top:894px;width:30px;height:30px;border-radius:50%;background:var(--white);box-shadow:0 2px 8px rgba(0,0,0,.2);display:flex;align-items:center;justify-content:center}
.arrow svg{width:10px;height:10px;fill:none;stroke:var(--ink);stroke-width:2}
.divider{top:1048px;left:64px;width:1076px;height:2px;background:var(--blue)}

/* apartments */
.apts-head{top:1124px}
.grid{position:absolute;top:1200px;left:232px;width:736px;display:grid;grid-template-columns:repeat(3,232px);gap:38px 20px}
.card .img{height:220px;position:relative}
.card .tag{position:absolute;right:10px;bottom:-12px;width:24px;height:24px;border-radius:50%;background:#c9c9c9;border:3px solid var(--white)}
.card .tag.blue{background:var(--blue)}
.card .meta{padding-top:12px}
.card .type{font-size:8px;color:var(--muted);text-transform:uppercase;letter-spacing:.5px}
.card h3{font-family:"Montserrat",sans-serif;font-size:12px;font-weight:600;color:var(--ink);margin:3px 0}
.card .price{font-size:8px;color:var(--blue)}
.view-all{position:absolute;top:1812px;left:560px;width:80px;height:26px;border:1.5px solid var(--ink);font-family:"Montserrat",sans-serif;font-size:8px;font-weight:600;display:flex;align-items:center;justify-content:center;letter-spacing:1px;color:var(--ink)}

/* video */
.video-band{top:1912px;height:808px;background:
 radial-gradient(ellipse 200px 160px at 80px 520px,#6b4a2e 0%,rgba(107,74,46,0) 100%),
 radial-gradient(ellipse 220px 120px at 1100px 560px,#6b5a3e 0%,rgba(107,90,62,0) 100%),
 linear-gradient(180deg,#1b5fa6 0%,#3a8cd0 30%,#8cc4ea 50%,#2c7fb8 62%,#23a1c0 82%,#7fd3d6 100%)}
.video-copy{position:absolute;top:2036px;left:280px;width:700px;display:flex;gap:60px;color:var(--white)}
.video-copy h2{font-family:"Playfair Display",serif;font-style:italic;font-size:24px;font-weight:400;line-height:1.2;text-transform:uppercase;width:240px;text-align:right}
.video-copy p{font-size:10px;line-height:1.7;width:360px}
.video-copy .more{display:block;margin-top:18px;font-family:"Montserrat",sans-serif;font-size:9px;font-weight:600;letter-spacing:1px}
.video-frame{position:absolute;top:2176px;left:232px;width:736px;height:360px;background:linear-gradient(180deg,#2b2b4a 0%,#7a4a6a 38%,#e08a4a 58%,#3a2a2a 100%);box-shadow:0 10px 30px rgba(0,0,0,.3)}
.play{position:absolute;right:28px;bottom:26px;display:flex;align-items:center;gap:10px;color:var(--white);font-family:"Montserrat",sans-serif;font-size:9px;font-weight:600;letter-spacing:1px}
.play .circle{width:34px;height:34px;border-radius:50%;border:1.5px solid var(--white);display:flex;align-items:center;justify-content:center}
.play svg{width:10px;height:10px;fill:var(--white)}

/* testimonials */
.tests-head{top:2752px}
.tests{position:absolute;top:2830px;left:300px;width:600px;display:grid;grid-template-columns:1fr 1fr;gap:60px;text-align:center}
.avatar{width:56px;height:56px;border-radius:50%;margin:0 auto 10px;background:linear-gradient(135deg,#c9a888,#7a5a40)}
.tests h4{font-family:"Montserrat",sans-serif;font-size:9px;font-weight:600;color:var(--ink);letter-spacing:.5px}
.tests .role{font-size:8px;color:var(--muted);margin:2px 0 12px}
.tests p{font-size:9px;line-height:1.7;color:var(--text)}
.pager{position:absolute;top:3030px;left:0;width:1200px;display:flex;justify-content:center;gap:12px;align-items:center;font-size:9px;color:var(--muted)}
.pager .dot{width:6px;height:6px;border-radius:50%;background:var(--line)}
.pager .dot.on{background:var(--ink)}

/* cta */
.cta{top:3120px;height:208px;background:
 radial-gradient(ellipse 360px 80px at 980px 110px,#4a6a3a 0%,rgba(74,106,58,0) 100%),
 linear-gradient(180deg,#3a5f88 0%,#6d95bc 40%,#1f5f90 62%,#16456e 100%);
 text-align:center;color:var(--white);padding-top:44px}
.cta .kicker{font-size:8px;letter-spacing:1px;text-transform:uppercase;opacity:.85}
.cta h2{font-family:"Playfair Display",serif;font-style:italic;font-size:22px;font-weight:400;margin:10px 0 16px}
.cta .btn{display:inline-block;background:var(--blue);padding:8px 18px;font-family:"Montserrat",sans-serif;font-size:8px;font-weight:600;letter-spacing:1px}

/* footer */
.footer{top:3328px;height:256px;background:var(--footer);color:var(--footer-text);padding:40px 240px 0}
.cols{display:grid;grid-template-columns:1.2fr 1fr 1fr 1.3fr;gap:30px}
.cols h5{font-family:"Montserrat",sans-serif;font-size:9px;color:var(--white);font-weight:600;letter-spacing:.5px;text-transform:uppercase;margin-bottom:14px}
.cols li{list-style:none;font-size:8px;line-height:2.1}
.cols .row{display:flex;gap:6px;align-items:flex-start;font-size:8px;line-height:1.6;margin-bottom:8px}
.cols .row svg{width:9px;height:9px;fill:var(--blue);flex:none;margin-top:2px}
.cols p{font-size:8px;line-height:1.7;margin-bottom:10px}
.subscribe{display:flex;height:24px}
.subscribe .email{flex:1;background:var(--white);font-size:8px;color:var(--muted);display:flex;align-items:center;padding-left:8px}
.subscribe .go{width:44px;background:var(--blue);color:var(--white);font-size:8px;display:flex;align-items:center;justify-content:center;font-weight:600}
.socials{display:flex;gap:10px;margin-top:14px}
.socials i{width:10px;height:10px;border-radius:50%;background:#5a5a5a;display:block}
.copyright{position:absolute;left:0;right:0;bottom:0;height:32px;border-top:1px solid #2a2a2a;display:flex;align-items:center;justify-content:center;font-size:8px;color:#666}
</style>
</head>
<body>
<div class="page">

  <div class="abs topbar">
    <div class="group">
      <span><svg viewBox="0 0 10 10"><path d="M2 0l2 2-1 1.5a6 6 0 0 0 3.5 3.5L8 6l2 2-1.5 2C4 10 0 6 0 1.5z"/></svg>+34 971 000 111</span>
      <span><svg viewBox="0 0 10 10"><path d="M0 2h10v6H0z M0 2l5 3 5-3" stroke="#fff" stroke-width=".8"/></svg>info@amberandslatevillas.example</span>
    </div>
    <div class="group"><span>EN</span></div>
  </div>

  <header class="abs header">
    <div class="brand"><span class="mark"></span>AMBER AND SLATE IBIZA</div>
    <nav class="nav">
      <span>HOME</span><span>ABOUT US</span><span>LOCATIONS</span><span>ALL PROPERTIES</span><span>REVIEWS</span><span>BLOG</span><span>CONTACT US</span>
      <span class="btn-outline">RESERVATIONS</span>
    </nav>
  </header>

  <section class="abs hero" role="img" aria-label="Photo of an Ibiza cove with pine trees, turquoise water and moored boats">
    <div class="hero-script">Villas &amp; The Countryside</div>
    <div class="hero-title">The best way to stay in Ibiza!</div>
    <div class="btn-ghost">LEARN MORE</div>
  </section>

  <form class="search">
    <div class="field"><label>Location</label><div class="input"><svg viewBox="0 0 10 10"><circle cx="5" cy="4" r="2.5"/></svg>Any location</div></div>
    <div class="field"><label>Check in</label><div class="input"><svg viewBox="0 0 10 10"><rect x="1" y="2" width="8" height="7"/></svg>Mon 01 Jul 2024</div></div>
    <div class="field"><label>Check out</label><div class="input"><svg viewBox="0 0 10 10"><rect x="1" y="2" width="8" height="7"/></svg>Mon 08 Jul 2024</div></div>
    <div class="field"><label>Bedrooms</label><div class="input"><svg viewBox="0 0 10 10"><path d="M1 8V3h8v5"/></svg>2 Bedrooms</div></div>
    <div class="field"><label>Bathrooms</label><div class="input"><svg viewBox="0 0 10 10"><path d="M1 5h8v3H1z"/></svg>1 Bath</div></div>
    <div class="field" style="display:grid;grid-template-columns:1fr 1fr;gap:10px">
      <div><label>Price range</label><div class="input">Any price</div></div>
      <div class="btn-search"><svg viewBox="0 0 10 10" width="10" height="10" fill="none" stroke="#fff" stroke-width="1.6"><circle cx="4" cy="4" r="3"/><path d="M6.3 6.3L9 9"/></svg>SEARCH</div>
    </div>
  </form>

  <div class="abs section-head explore-head">
    <div class="ghost">Explore Ibiza</div>
    <h2>Experience the finest villa</h2>
  </div>

  <div class="abs carousel">
    <div class="slide" role="img" aria-label="Photo of white houses above a blue bay" style="background:linear-gradient(180deg,#7fb2de,#e8eef4 45%,#2a6aa8)"><div class="cap">SANT ANTONI BAY</div></div>
    <div class="slide" role="img" aria-label="Photo of colourful harbour houses" style="background:linear-gradient(180deg,#9cc7e8,#d9a27a 45%,#3a7aa8)"><div class="cap">EIVISSA OLD TOWN</div></div>
    <div class="slide" role="img" aria-label="Photo of a rocky islet rising from the sea" style="background:linear-gradient(180deg,#6fa6d6,#8a8f9a 50%,#1f5e94)"><div class="cap">ES VEDRÀ</div></div>
    <div class="slide" role="img" aria-label="Photo of a whitewashed village church" style="background:linear-gradient(180deg,#8cbfe6,#efe9df 50%,#8a9a6a)"><div class="cap">SANTA GERTRUDIS</div></div>
    <div class="slide" role="img" aria-label="Photo of a couple relaxing by the sea" style="background:linear-gradient(180deg,#a8d2ee,#e0c2a0 55%,#4a8ab8)"><div class="cap">ROMANTIC ESCAPE</div></div>
  </div>
  <div class="arrow" style="left:50px"><svg viewBox="0 0 10 10"><path d="M6.5 1.5L3 5l3.5 3.5"/></svg></div>
  <div class="arrow" style="left:1122px"><svg viewBox="0 0 10 10"><path d="M3.5 1.5L7 5 3.5 8.5"/></svg></div>
  <div class="abs divider"></div>

  <div class="abs section-head apts-head">
    <div class="ghost">Our flats are great</div>
    <h2>Popular apartments</h2>
  </div>

  <div class="grid">
    <article class="card"><div class="img" role="img" aria-label="Photo of a white villa under blue sky" style="background:linear-gradient(180deg,#4a8ad6,#f2f2ee 55%,#6a8a4a)"><span class="tag"></span></div>
      <div class="meta"><div class="type">Villa</div><h3>Villa Can Sereno</h3><div class="price">From €250 / night</div></div></article>
    <article class="card"><div class="img" role="img" aria-label="Photo of a rustic stone interior" style="background:linear-gradient(180deg,#6a5444,#a88a6a 60%,#4a3a2e)"><span class="tag blue"></span></div>
      <div class="meta"><div class="type">Agroturismo</div><h3>Agroturismo Can Olivar</h3><div class="price">From €180 / night</div></div></article>
    <article class="card"><div class="img" role="img" aria-label="Photo of a private swimming pool with terrace" style="background:linear-gradient(180deg,#d4a26a,#3aa0d0 50%,#1a7ab8)"><span class="tag"></span></div>
      <div class="meta"><div class="type">Villa</div><h3>Villa Les Tres Pins</h3><div class="price">From €320 / night</div></div></article>
    <article class="card"><div class="img" role="img" aria-label="Photo of a pool with loungers and garden" style="background:linear-gradient(180deg,#5a8a4a,#2ab0d6 55%,#c8b89a)"><span class="tag"></span></div>
      <div class="meta"><div class="type">Villa</div><h3>Villa Can Marès</h3><div class="price">From €290 / night</div></div></article>
    <article class="card"><div class="img" role="img" aria-label="Photo of a shaded dining terrace" style="background:linear-gradient(180deg,#8a6a4a,#c89a6a 50%,#5a6a3a)"><span class="tag blue"></span></div>
      <div class="meta"><div class="type">Villa</div><h3>Villa Cala Morna</h3><div class="price">From €270 / night</div></div></article>
    <article class="card"><div class="img" role="img" aria-label="Photo of a bright living room" style="background:linear-gradient(180deg,#d8cab4,#a8845e 55%,#6a4a34)"><span class="tag"></span></div>
      <div class="meta"><div class="type">Villa</div><h3>Villa Can Roure</h3><div class="price">From €240 / night</div></div></article>
  </div>
  <div class="view-all">VIEW ALL</div>

  <section class="abs video-band" role="img" aria-label="Photo of the Mediterranean coast with rocky headlands under a blue sky"></section>
  <div class="video-copy">
    <h2>Villas &amp;<br>The Countryside</h2>
    <p>Local, family-run and always on the island: our team welcomes every guest in person, shares the best beaches and restaurants, and stays on call for the whole stay. Private pools, gardens and space no hotel can match.<span class="more">READ MORE</span></p>
  </div>
  <div class="video-frame" role="img" aria-label="Video still of a person raising hands against an Ibiza sunset over the sea">
    <div class="play"><span class="circle"><svg viewBox="0 0 10 10"><path d="M2 1l7 4-7 4z"/></svg></span>PLAY NOW</div>
  </div>

  <div class="abs section-head tests-head">
    <div class="ghost">What clients say</div>
    <h2>Testimonials</h2>
  </div>
  <div class="tests">
    <div>
      <div class="avatar" role="img" aria-label="Guest portrait"></div>
      <h4>MARTA LINDQVIST</h4><div class="role">Guest from Sweden</div>
      <p>We were met at the villa by the team and given maps, tips and a warm welcome. The pool and garden were perfect and every question was answered within minutes. We will book again next summer.</p>
    </div>
    <div>
      <div class="avatar" role="img" aria-label="Guest portrait"></div>
      <h4>JONAS BECKER</h4><div class="role">Guest from Germany</div>
      <p>Booking directly gave us the best price and great service. The house had more space than any hotel, and the local advice helped us find quiet coves and wonderful restaurants by the sea.</p>
    </div>
  </div>
  <div class="pager"><span>‹</span><span class="dot on"></span><span class="dot"></span><span>›</span></div>

  <section class="abs cta" role="img" aria-label="Photo of a hillside village above the blue sea">
    <div class="kicker">Book direct</div>
    <h2>Lorem Ipsum is simply dummy text of the printing and typesetting industry.</h2>
    <span class="btn">GET STARTED</span>
  </section>

  <footer class="abs footer">
    <div class="cols">
      <div>
        <h5>Contact us</h5>
        <div class="row"><svg viewBox="0 0 10 10"><path d="M0 2h10v6H0z"/></svg>info@amberandslatevillas.example</div>
        <div class="row"><svg viewBox="0 0 10 10"><path d="M2 0l2 2-1 1.5a6 6 0 0 0 3.5 3.5L8 6l2 2-1.5 2C4 10 0 6 0 1.5z"/></svg>+34 971 000 111<br>+34 600 000 222</div>
        <div class="row"><svg viewBox="0 0 10 10"><path d="M5 0a3.5 3.5 0 0 1 3.5 3.5C8.5 6 5 10 5 10S1.5 6 1.5 3.5A3.5 3.5 0 0 1 5 0z"/></svg>Carrer de la Mar 12, 07800 Eivissa, Illes Balears</div>
      </div>
      <div>
        <h5>Quick links</h5>
        <ul><li>Home</li><li>About us</li><li>Locations</li><li>All properties</li><li>Reviews</li><li>Contact us</li></ul>
      </div>
      <div>
        <h5>Our policy</h5>
        <ul><li>Terms of booking</li><li>Privacy policy</li><li>Cookie policy</li><li>Cancellations</li><li>FAQ</li></ul>
      </div>
      <div>
        <h5>Newsletter</h5>
        <p>Subscribe for offers, island news and the best direct prices on our villas.</p>
        <div class="subscribe"><span class="email">Your email</span><span class="go">SEND</span></div>
        <div class="socials"><i></i><i></i><i></i><i></i></div>
      </div>
    </div>
    <div class="copyright">© 2024 Amber and Slate Ibiza. All rights reserved.</div>
  </footer>

</div>
</body>
</html>
```